Business Card Design

My business is writing crime novels to entertain readers. I write legal thrillers and mysteries. I need a card for publishers, agents, other authors, and media.

Industry/Entity Type

Legal

Contact Information for Business Card

Paul Derrow
www.derrowfiction.example
pauljderrow@inkpost.example
0064 27 5190472

```html
<!DOCTYPE html>
<html lang="en">
<head>
<meta charset="utf-8">
<title>Paul Derrow — Business Card</title>
<link rel="stylesheet" href="https://fonts.googleapis.com/css2?family=Cabin+Condensed:wght@700&family=Cabin:wght@600&display=swap">
<style>
  :root {
    --page-bg: #e9e6e1;
    --card-black: #050505;
    --card-glow: #2c2c2c;
    --tape-yellow: #f5e616;
    --ink-black: #0a0a0a;
    --frame-grey: #3a3a3a;
    --portrait-grey: #8d8d8d;
  }
  html, body {
    margin: 0;
    width: 1200px;
    height: 1181px;
    overflow: hidden;
    background: var(--page-bg);
  }
  .canvas {
    position: relative;
    width: 1200px;
    height: 1181px;
  }
  .business-card {
    position: absolute;
    left: 50px;
    top: 274px;
    width: 1100px;
    height: 633px;
    box-shadow: 0 10px 30px rgba(0,0,0,0.25);
  }
  .tape-name {
    font-family: "Cabin Condensed", "Arial Narrow", sans-serif;
    font-weight: 700;
    font-size: 78px;
    fill: var(--ink-black);
  }
  .contact-line {
    font-family: "Cabin", "Gill Sans", sans-serif;
    font-weight: 600;
    font-size: 15.5px;
    fill: var(--tape-yellow);
  }
</style>
</head>
<body>
<div class="canvas">
  <svg class="business-card" viewBox="0 0 786 452" xmlns="http://www.w3.org/2000/svg">
    <defs>
      <radialGradient id="card-glow" cx="0.55" cy="0.4" r="0.7">
        <stop offset="0" stop-color="var(--card-glow)"/>
        <stop offset="1" stop-color="var(--card-black)"/>
      </radialGradient>
      <clipPath id="card-edge">
        <rect width="786" height="452"/>
      </clipPath>
    </defs>

    <g clip-path="url(#card-edge)">
      <rect class="card-face" width="786" height="452" fill="url(#card-glow)"/>

      <!-- portrait block -->
      <rect class="portrait-accent" x="40" y="40" width="185" height="198"
            fill="var(--tape-yellow)" transform="rotate(-11 132 139)"/>
      <rect class="portrait-frame" x="41" y="38" width="180" height="204" fill="var(--frame-grey)"/>
      <rect class="portrait" x="48" y="45" width="166" height="190" fill="var(--portrait-grey)"
            role="img" aria-label="Portrait photograph of the author"/>

      <!-- crime-scene tape -->
      <g class="tape" transform="translate(0 366) rotate(-14.4)">
        <rect x="-60" y="-50" width="960" height="100" fill="var(--tape-yellow)"/>
        <text class="tape-name" x="-6" y="28" text-anchor="end">ROW</text>
        <text class="tape-name" x="196" y="28">PAUL DERROW</text>
        <text class="tape-name" x="705" y="28">PAU</text>
        <text class="contact-line" x="78" y="72">◆ 0064 27 5190472  ◆  pauljderrow@inkpost.example  ◆  www.derrowfiction.example</text>
      </g>
    </g>
  </svg>
</div>
</body>
</html>
```